Website for a Psychologist in Private Practice

I need a cool web design for my website: www.drkalvoric.com. I would like it to look professional. Keep all the current content and add: Space for video; radio spots (see Silver Cedar Tunes Logo below for those); Quick Inquiry; Friendora link; 5 star rating on Rivo; a map; reviews from former patients. I am open to suggestions.

Target Market(s)

Those seeking individual and marital counseling.

Industry/Entity Type

Mental Health

Number of Pages Required

1 page

Font styles to use
Sans Serif
Other font styles liked:
• I'm open but no hard to read script

Requirements
Must have
• All the content on my home page with link for video and radio spots. List services and degrees and expertices (pics not necessary).
Nice to have
• A video of me and radio conversations (logo of Silver Cedar Tunes radio attached).
Should not have
• Cartoons, comedy, etc.... I don't need pictures of services (marital, depression, etc...) Just list those.

```html
<!DOCTYPE html>
<html lang="en">
<head>
<meta charset="utf-8">
<title>Dr. Lena R. Kalvoric – Clinical Psychologist</title>
<link rel="stylesheet" href="https://fonts.googleapis.com/css2?family=Open+Sans:ital,wght@0,400;0,600;0,700;1,400;1,600&display=swap">
<style>
:root{
  --blue:#1565c0;
  --blue-dark:#0d57b0;
  --gold:#b9a04a;
  --gold-text:#b39a3c;
  --ink:#222;
  --body:#444;
  --light:#f2f2f2;
  --footer:#444444;
  --line:#5a5a5a;
  --white:#fff;
}
*{box-sizing:border-box;margin:0;padding:0}
html,body{width:1200px;height:2384px;overflow:hidden}
body{font-family:"Open Sans",Arial,sans-serif;color:var(--body);background:var(--white);position:relative}
.inner{width:1052px;margin:0 auto;position:relative}

/* top bar */
.topbar{height:38px;background:var(--blue);color:var(--white);font-size:13px;display:flex;justify-content:flex-end;align-items:center;padding-right:75px;gap:0}
.topbar .item{display:flex;align-items:center;gap:7px;padding:0 12px;border-left:1px solid rgba(255,255,255,.6)}
.topbar .item:first-child{border-left:none}
.topbar svg{width:13px;height:13px;fill:var(--white)}

/* header */
.header{height:75px;background:#f4f4f4;display:flex;align-items:center;justify-content:space-between;padding:0 75px 0 88px}
.brand{font-size:29px;font-weight:600;color:var(--blue)}
.nav{display:flex;gap:50px;font-size:15px;font-weight:600;color:var(--ink)}
.nav .active{color:var(--gold-text)}

/* hero */
.hero{height:477px;position:relative;background:linear-gradient(180deg,#7fc3cf 0%,#a9d6d6 35%,#d9cdb5 70%,#cbb898 100%)}
.hero-photo{position:absolute;left:75px;top:28px;width:689px;height:420px;border:3px solid #333;border-radius:4px;background:linear-gradient(100deg,#b99d85 0%,#8c7a6c 45%,#44505f 80%,#3a4352 100%)}
.hero-copy{position:absolute;left:22px;top:145px;color:var(--white)}
.hero-copy h1{font-size:35px;line-height:38px;font-weight:700;letter-spacing:.3px}
.btn-gold{display:inline-block;margin-top:18px;background:var(--gold);color:var(--white);font-size:15px;font-weight:700;padding:9px 16px}
.hero-video{position:absolute;left:794px;top:28px;width:331px;height:198px;border:3px solid #333;border-radius:4px;background:linear-gradient(160deg,#c9b88e,#a5896a 55%,#6f5a4a);overflow:hidden}
.play{position:absolute;left:134px;top:58px;width:62px;height:62px;border-radius:50%;background:rgba(120,120,120,.75)}
.play svg{position:absolute;left:22px;top:17px}
.progress{position:absolute;left:12px;right:12px;bottom:10px;height:5px;background:#999}
.progress span{display:block;width:40%;height:100%;background:#e8c437}
.hero-radio{position:absolute;left:794px;top:249px;width:331px;height:199px;border:3px solid #333;border-radius:4px;background:linear-gradient(135deg,#f7a35a,#ec7e3a 60%,#e46c2c)}
.radio-icon{position:absolute;left:63px;top:38px}
.radio-title{position:absolute;left:168px;top:38px;color:var(--white);font-size:32px;line-height:34px;font-weight:700}
.radio-band{position:absolute;left:24px;top:134px;width:285px;height:30px;background:#e8197a;color:var(--white);font-size:20px;font-weight:700;text-align:center;line-height:30px}
.radio-sub{position:absolute;left:0;right:0;top:166px;text-align:center;color:var(--white);font-size:15px;font-weight:600}

/* about */
.about{height:517px;background:var(--light);padding-top:48px;text-align:center}
.section-title{font-size:26px;font-weight:700;color:var(--ink);letter-spacing:.5px}
.about p{font-size:14.3px;line-height:24px;width:1010px;margin:14px auto 0;color:#555}
.about p b{color:var(--ink)}

/* inquiry */
.inquiry{height:121px;background:var(--gold);display:flex;align-items:center;padding-left:95px}
.inq-label{color:var(--white);width:256px}
.inq-label small{display:block;font-size:18px}
.inq-label strong{display:block;font-size:25px;font-weight:600;letter-spacing:.5px}
.field{width:190px;height:36px;background:var(--white);border-radius:3px;margin-right:17px;font-size:13px;color:#555;padding:9px 12px}
.btn-blue{margin-left:4px;width:124px;height:36px;background:var(--blue-dark);color:var(--white);border-radius:3px;font-size:17px;font-weight:700;text-align:center;line-height:36px}

/* reviews */
.reviews{height:412px;padding-top:52px;text-align:center;position:relative}
.review-row{display:flex;gap:25px;margin:36px 0 0 73px}
.review{width:334px;text-align:left}
.review-card{height:158px;background:#f8f8f8;border:1px solid #ddd;border-radius:3px;padding:26px 30px;font-size:14px;line-height:21px;color:#333;position:relative}
.review-card:after{content:"";position:absolute;left:60px;bottom:-12px;width:20px;height:20px;background:#f8f8f8;border-right:1px solid #ddd;border-bottom:1px solid #ddd;transform:skewX(35deg) rotate(0deg);clip-path:polygon(0 0,100% 0,0 100%)}
.reviewer{display:flex;align-items:center;gap:12px;margin:14px 0 0 54px}
.avatar{width:70px;height:70px;border-radius:50%;border:3px solid #ccc;background:linear-gradient(160deg,#b58b7a,#5f3e3a)}
.reviewer .name{font-style:italic;font-weight:600;color:var(--gold-text);font-size:15px}
.reviewer .role{font-style:italic;font-size:13px;color:#555}
.arrow{position:absolute;top:266px}
.arrow.left{left:38px}
.arrow.right{right:38px}

/* expertise */
.expertise{height:243px;background:var(--light);position:relative}
.exp-panel{position:absolute;left:0;top:0;width:625px;height:243px;background:var(--blue);clip-path:polygon(0 0,100% 0,92.5% 100%,0 100%)}
.exp-col{position:absolute;top:50px;color:var(--white)}
.exp-col h3{font-size:22px;font-weight:700;letter-spacing:.3px;margin-bottom:8px}
.exp-col li{list-style:none;font-size:15px;font-weight:600;line-height:27.5px;display:flex;align-items:center;gap:10px}
.exp-col li svg{width:15px;height:12px}
.partner{position:absolute;background:#d4d4d4;border-radius:6px}

/* credentials */
.credentials{height:156px;text-align:center;padding-top:33px}
.credentials h4{font-size:18px;font-weight:600;color:var(--ink);letter-spacing:.3px}
.credentials p{font-size:15px;color:var(--blue);line-height:27px;font-weight:600}
.credentials p:first-of-type{margin-top:8px}

/* footer */
.footer{height:291px;background:var(--footer);color:var(--white);display:flex;padding:50px 0 0 73px;gap:0}
.fcol{width:358px}
.fcol h5{font-size:13.5px;font-weight:700;letter-spacing:.3px;padding-bottom:12px;border-bottom:1px solid var(--line);width:334px}
.contact-row{display:flex;gap:14px;align-items:flex-start;margin-top:18px;font-size:14px;line-height:20px}
.contact-row svg{width:20px;height:20px;fill:var(--white);flex:none}
.contact-row.big{font-size:17px;align-items:center}
.map{margin-top:18px;width:334px;height:160px;background:linear-gradient(120deg,#e4e1d8,#d8d4c8 50%,#cfd9c4)}
.links{margin-top:17px;font-size:14px;line-height:24px}

/* bottom bar */
.bottombar{height:54px;background:var(--gold);color:var(--white);display:flex;align-items:center;justify-content:space-between;padding:0 75px;font-size:14px}
.social{display:flex;gap:26px}
.social span{display:flex;align-items:center;gap:8px}
.social i{display:inline-block;width:12px;height:12px;border-radius:50%;background:var(--white)}
</style>
</head>
<body>

<div class="topbar">
  <div class="item"><svg viewBox="0 0 24 24"><path d="M12 2a7 7 0 0 0-7 7c0 5 7 13 7 13s7-8 7-13a7 7 0 0 0-7-7zm0 9.5A2.5 2.5 0 1 1 12 6.5a2.5 2.5 0 0 1 0 5z"/></svg>418 Heron Lane, Suite 210 Bayview, CA 92410</div>
  <div class="item"><svg viewBox="0 0 24 24"><path d="M2 5h20v14H2z M2 5l10 8 10-8" fill="none" stroke="#fff" stroke-width="2"/></svg>lk@drkalvoric.com</div>
  <div class="item"><svg viewBox="0 0 24 24"><path d="M6.6 10.8a15 15 0 0 0 6.6 6.6l2.2-2.2a1 1 0 0 1 1-.25 11.4 11.4 0 0 0 3.6.57 1 1 0 0 1 1 1V20a1 1 0 0 1-1 1A17 17 0 0 1 3 4a1 1 0 0 1 1-1h3.5a1 1 0 0 1 1 1c0 1.25.2 2.45.57 3.57a1 1 0 0 1-.25 1z"/></svg>(555) 318 2046</div>
</div>

<header class="header">
  <div class="brand">Dr. Lena R. Kalvoric</div>
  <nav class="nav">
    <span class="active">HOME</span><span>SESSIONS</span><span>RESOURCES</span><span>BIO</span><span>CONTACT</span>
  </nav>
</header>

<section class="hero">
  <div class="hero-photo" role="img" aria-label="Photo of a client talking with a therapist over paperwork">
    <div class="hero-copy">
      <h1>HELPING YOU<br>TO FIND YOUR OWN<br>SOLUTIONS</h1>
      <span class="btn-gold">LEARN MORE</span>
    </div>
  </div>
  <div class="hero-video" role="img" aria-label="Video still of the psychologist">
    <div class="play"><svg width="24" height="28" viewBox="0 0 24 28"><path d="M0 0l24 14L0 28z" fill="#fff"/></svg></div>
    <div class="progress"><span></span></div>
  </div>
  <div class="hero-radio">
    <svg class="radio-icon" width="86" height="68" viewBox="0 0 86 68">
      <line x1="14" y1="18" x2="66" y2="2" stroke="#fff" stroke-width="4" stroke-linecap="round"/>
      <rect x="2" y="18" width="82" height="48" rx="8" fill="#fff"/>
      <circle cx="60" cy="42" r="14" fill="#ec7e3a"/>
      <rect x="12" y="30" width="28" height="6" fill="#ec7e3a"/>
      <rect x="12" y="44" width="4" height="12" fill="#ec7e3a"/><rect x="20" y="44" width="4" height="12" fill="#ec7e3a"/><rect x="28" y="44" width="4" height="12" fill="#ec7e3a"/><rect x="36" y="44" width="4" height="12" fill="#ec7e3a"/>
    </svg>
    <div class="radio-title">RADIO<br>SPOTS</div>
    <div class="radio-band">Silver Cedar Tunes</div>
    <div class="radio-sub">With Mira and Tess</div>
  </div>
</section>

<section class="about">
  <h2 class="section-title">ABOUT DR. LENA R. KALVORIC</h2>
  <p>I'm so glad you are here.&nbsp; Choosing to see a professional for issues in your life can be difficult but also possibly life changing. Many postpone seeking help because they believe doing so acknowledges failure on their part.&nbsp; Reallly?&nbsp; We seek the help of experts all the time (contractors, mechanics, chefs, etc...) and what is more important than your life? Consulting with a neutral party to act in your best interest can be time well spent.&nbsp; So if you are willing to take the time to invest in counseling, make sure that it is with<br>someone that is worth your time.</p>
  <p>Choose a licensed psychologist with a doctoral degree (Ph.D. or PsyD.) - both have over 10 years of education in the field of psychology, extensive internships and comprehensive licensing exams.&nbsp; Others have far less education if any.&nbsp; Also, consider the therapist's approach to therapy.&nbsp; I use a straightforward approach (psychobabble available upon request) with brief, solution-oriented sessions.</p>
  <p>Experience also separates good psychologists from others with fewer and more proficient sessions.&nbsp; My&nbsp; 20+ years of professional experience and my life experience contributes to the empathetic perspective I use to relate to each person I see.&nbsp; I also believe it is the reason 90% of my practice is referral based and why many other psychologists in the area seek my services.</p>
  <p><b>DO NOT COMPROMISE.</b>&nbsp; Find an educated, licensed, experienced professional that you can relate to. Think about what it took to get you here and the importance resolving this issue can have on your life.</p>
</section>

<section class="inquiry">
  <div class="inq-label"><small>Contact Us Today for Your</small><strong>QUICK INQUIRY</strong></div>
  <div class="field">Name</div>
  <div class="field">Phone</div>
  <div class="field">Email</div>
  <div class="btn-blue">SUBMIT</div>
</section>

<section class="reviews">
  <h2 class="section-title">REVIEWS FROM PATIENTS</h2>
  <svg class="arrow left" width="12" height="22" viewBox="0 0 12 22"><path d="M11 1L1 11l10 10" fill="none" stroke="#333" stroke-width="2"/></svg>
  <svg class="arrow right" width="12" height="22" viewBox="0 0 12 22"><path d="M1 1l10 10L1 21" fill="none" stroke="#333" stroke-width="2"/></svg>
  <div class="review-row">
    <div class="review">
      <div class="review-card">Lorem ipsum dolor sit amet, consectetuer adipiscing elit, sed diam nonummy nibh euismod tincidunt ut laoreet dolore magna aliquam erat volutpat. Ut wisi enim ad minim veniam, quis nostrud.</div>
      <div class="reviewer"><div class="avatar" role="img" aria-label="Patient portrait"></div><div><div class="name">Nora B.</div><div class="role">Lorem ipsum dolor</div></div></div>
    </div>
    <div class="review">
      <div class="review-card">Lorem ipsum dolor sit amet, consectetuer adipiscing elit, sed diam nonummy nibh euismod tincidunt ut laoreet dolore magna aliquam erat volutpat. Ut wisi enim ad minim veniam, quis nostrud.</div>
      <div class="reviewer"><div class="avatar" role="img" aria-label="Patient portrait"></div><div><div class="name">Nora B.</div><div class="role">Lorem ipsum dolor</div></div></div>
    </div>
    <div class="review">
      <div class="review-card">Lorem ipsum dolor sit amet, consectetuer adipiscing elit, sed diam nonummy nibh euismod tincidunt ut laoreet dolore magna aliquam erat volutpat. Ut wisi enim ad minim veniam, quis nostrud.</div>
      <div class="reviewer"><div class="avatar" role="img" aria-label="Patient portrait"></div><div><div class="name">Nora B.</div><div class="role">Lorem ipsum dolor</div></div></div>
    </div>
  </div>
</section>

<section class="expertise">
  <div class="exp-panel"></div>
  <div class="exp-col" style="left:72px">
    <h3>EXPERTISE</h3>
    <ul>
      <li><svg viewBox="0 0 15 12"><path d="M1 6l4 4 9-9" fill="none" stroke="#e0b53a" stroke-width="2.5"/></svg>Dating</li>
      <li><svg viewBox="0 0 15 12"><path d="M1 6l4 4 9-9" fill="none" stroke="#e0b53a" stroke-width="2.5"/></svg>Marriage</li>
      <li><svg viewBox="0 0 15 12"><path d="M1 6l4 4 9-9" fill="none" stroke="#e0b53a" stroke-width="2.5"/></svg>Parenting</li>
      <li><svg viewBox="0 0 15 12"><path d="M1 6l4 4 9-9" fill="none" stroke="#e0b53a" stroke-width="2.5"/></svg>Professional</li>
    </ul>
  </div>
  <div class="exp-col" style="left:300px">
    <h3>RELATIONSHIPS</h3>
    <ul>
      <li><svg viewBox="0 0 15 12"><path d="M1 6l4 4 9-9" fill="none" stroke="#e0b53a" stroke-width="2.5"/></svg>Depression &amp; Anxiety Issues</li>
      <li><svg viewBox="0 0 15 12"><path d="M1 6l4 4 9-9" fill="none" stroke="#e0b53a" stroke-width="2.5"/></svg>Personality Disorders</li>
      <li><svg viewBox="0 0 15 12"><path d="M1 6l4 4 9-9" fill="none" stroke="#e0b53a" stroke-width="2.5"/></svg>Life Management</li>
    </ul>
  </div>
  <div class="partner" style="left:640px;top:68px;width:220px;height:100px"></div>
  <div class="partner" style="left:888px;top:98px;width:215px;height:60px"></div>
</section>

<section class="credentials">
  <h4>CLINICAL PSYCHOLOGIST - California # PSY20583</h4>
  <p>Doctoral Degree in Clinical Psychology | Masters Degree in Counseling Psychology</p>
  <p>Doctoral Internship, Lakeside Medical Center | Masters Internship, Westbrook Clinic</p>
</section>

<footer class="footer">
  <div class="fcol">
    <h5>CONTACT INFORMATION</h5>
    <div class="contact-row" style="margin-top:20px"><svg viewBox="0 0 24 24"><path d="M12 2a7 7 0 0 0-7 7c0 5 7 13 7 13s7-8 7-13a7 7 0 0 0-7-7zm0 9.5A2.5 2.5 0 1 1 12 6.5a2.5 2.5 0 0 1 0 5z"/></svg><div>418 Heron Lane, Suite 210<br>Bayview, CA 92410</div></div>
    <div class="contact-row big" style="margin-top:26px"><svg viewBox="0 0 24 24"><path d="M6.6 10.8a15 15 0 0 0 6.6 6.6l2.2-2.2a1 1 0 0 1 1-.25 11.4 11.4 0 0 0 3.6.57 1 1 0 0 1 1 1V20a1 1 0 0 1-1 1A17 17 0 0 1 3 4a1 1 0 0 1 1-1h3.5a1 1 0 0 1 1 1c0 1.25.2 2.45.57 3.57a1 1 0 0 1-.25 1z"/></svg>(555) 318 2046</div>
    <div class="contact-row" style="margin-top:28px;align-items:center"><svg viewBox="0 0 24 24"><path d="M2 4h20v16H2z" /><path d="M2 5l10 8 10-8" fill="none" stroke="#444" stroke-width="2"/></svg>lk@drkalvoric.com</div>
  </div>
  <div class="fcol">
    <h5>FIND US ON MAP</h5>
    <div class="map" role="img" aria-label="Street map showing the office location"></div>
  </div>
  <div class="fcol">
    <h5>QUICK LINKS</h5>
    <div class="links">Home<br>Sessions<br>Resources<br>Bio<br>Contact</div>
  </div>
</footer>

<div class="bottombar">
  <span>©2016 Dr. Lena R. Kalvoric. All Rights Reserved.</span>
  <div class="social"><span><i></i>Rivo</span><span><i></i>Friendora</span><span><i></i>Chirply</span></div>
</div>

</body>
</html>
```